" Fazer o calendário de parede conforme o anexo abaixo sendo que a parte para fazer o cabeçalho tem que ter a medida 41cm de comprimento por 11,5cm de altura "

```html
<!DOCTYPE html>
<html lang="pt-BR">
<head>
<meta charset="utf-8">
<title>Calendário de parede 2025 · Pomar Verde</title>
<link href="https://fonts.googleapis.com/css2?family=Raleway:wght@400;500;700&display=swap" rel="stylesheet">
<style>
:root{
  --backdrop:#ecebe8;
  --sheet:#ffffff;
  --ink:#4a4a4a;
  --day:#6b6b6b;
  --band:#fbe3d4;
  --band-ink:#e0793f;
  --fruit-deep:#c73a12;
  --fruit-mid:#f06a1c;
  --fruit-light:#f59a3a;
  --melon:#e5464b;
  --brand:#ffffff;
}
*{margin:0;padding:0;box-sizing:border-box}
html,body{width:1200px;height:1200px;overflow:hidden}
body{background:var(--backdrop);font-family:"Raleway",sans-serif;font-variant-numeric:lining-nums tabular-nums;display:flex;align-items:center;justify-content:center}
.calendar{width:760px;height:1120px;background:var(--sheet);box-shadow:0 10px 30px rgba(0,0,0,.12);display:flex;flex-direction:column}
.header{position:relative;height:213px;flex:none}
.header-photo{position:absolute;inset:0}
.brand{position:absolute;left:44px;top:50%;transform:translateY(-50%);display:flex;align-items:center;gap:14px}
.brand-dot{width:22px;height:22px;border-radius:50%;background:var(--brand)}
.brand-name{font-weight:700;font-size:48px;color:var(--brand);letter-spacing:.5px}
.months{flex:1;display:grid;grid-template-columns:repeat(3,1fr);grid-template-rows:repeat(4,1fr);column-gap:40px;padding:34px 50px 28px}
.month h2{font-weight:500;font-size:20px;color:var(--ink);margin-bottom:8px}
.weekdays,.days{display:grid;grid-template-columns:repeat(7,1fr);text-align:center}
.weekdays{background:var(--band);color:var(--band-ink);font-size:11px;font-weight:700;line-height:18px;margin-bottom:4px}
.days i{font-style:normal;font-size:12px;font-weight:500;color:var(--day);line-height:21px;font-variant-numeric:lining-nums tabular-nums}
.o1{grid-column-start:2}.o2{grid-column-start:3}.o3{grid-column-start:4}
.o4{grid-column-start:5}.o5{grid-column-start:6}.o6{grid-column-start:7}
</style>
</head>
<body>
<main class="calendar">
  <header class="header">
    <svg class="header-photo" role="img" aria-label="Fotografia de tangerinas empilhadas com fatia de melancia e morangos no canto direito" width="760" height="213" viewBox="0 0 760 213">
      <defs>
        <linearGradient id="fruit" x1="0" y1="0" x2="1" y2="1">
          <stop offset="0" stop-color="#c73a12"/>
          <stop offset=".5" stop-color="#f06a1c"/>
          <stop offset="1" stop-color="#f59a3a"/>
        </linearGradient>
        <radialGradient id="accent" cx=".88" cy=".3" r=".25">
          <stop offset="0" stop-color="#e5464b"/>
          <stop offset="1" stop-color="#e5464b" stop-opacity="0"/>
        </radialGradient>
      </defs>
      <rect width="760" height="213" fill="url(#fruit)"/>
      <rect width="760" height="213" fill="url(#accent)"/>
    </svg>
    <div class="brand"><span class="brand-dot"></span><span class="brand-name">Pomar Verde</span></div>
  </header>

  <section class="months">
    <article class="month"><h2>Janeiro</h2><div class="weekdays"><span>D</span><span>S</span><span>T</span><span>Q</span><span>Q</span><span>S</span><span>S</span></div>
      <div class="days"><i class="o3">1</i><i>2</i><i>3</i><i>4</i><i>5</i><i>6</i><i>7</i><i>8</i><i>9</i><i>10</i><i>11</i><i>12</i><i>13</i><i>14</i><i>15</i><i>16</i><i>17</i><i>18</i><i>19</i><i>20</i><i>21</i><i>22</i><i>23</i><i>24</i><i>25</i><i>26</i><i>27</i><i>28</i><i>29</i><i>30</i><i>31</i></div></article>
    <article class="month"><h2>Fevereiro</h2><div class="weekdays"><span>D</span><span>S</span><span>T</span><span>Q</span><span>Q</span><span>S</span><span>S</span></div>
      <div class="days"><i class="o6">1</i><i>2</i><i>3</i><i>4</i><i>5</i><i>6</i><i>7</i><i>8</i><i>9</i><i>10</i><i>11</i><i>12</i><i>13</i><i>14</i><i>15</i><i>16</i><i>17</i><i>18</i><i>19</i><i>20</i><i>21</i><i>22</i><i>23</i><i>24</i><i>25</i><i>26</i><i>27</i><i>28</i></div></article>
    <article class="month"><h2>Março</h2><div class="weekdays"><span>D</span><span>S</span><span>T</span><span>Q</span><span>Q</span><span>S</span><span>S</span></div>
      <div class="days"><i class="o6">1</i><i>2</i><i>3</i><i>4</i><i>5</i><i>6</i><i>7</i><i>8</i><i>9</i><i>10</i><i>11</i><i>12</i><i>13</i><i>14</i><i>15</i><i>16</i><i>17</i><i>18</i><i>19</i><i>20</i><i>21</i><i>22</i><i>23</i><i>24</i><i>25</i><i>26</i><i>27</i><i>28</i><i>29</i><i>30</i><i>31</i></div></article>

    <article class="month"><h2>Abril</h2><div class="weekdays"><span>D</span><span>S</span><span>T</span><span>Q</span><span>Q</span><span>S</span><span>S</span></div>
      <div class="days"><i class="o2">1</i><i>2</i><i>3</i><i>4</i><i>5</i><i>6</i><i>7</i><i>8</i><i>9</i><i>10</i><i>11</i><i>12</i><i>13</i><i>14</i><i>15</i><i>16</i><i>17</i><i>18</i><i>19</i><i>20</i><i>21</i><i>22</i><i>23</i><i>24</i><i>25</i><i>26</i><i>27</i><i>28</i><i>29</i><i>30</i></div></article>
    <article class="month"><h2>Maio</h2><div class="weekdays"><span>D</span><span>S</span><span>T</span><span>Q</span><span>Q</span><span>S</span><span>S</span></div>
      <div class="days"><i class="o4">1</i><i>2</i><i>3</i><i>4</i><i>5</i><i>6</i><i>7</i><i>8</i><i>9</i><i>10</i><i>11</i><i>12</i><i>13</i><i>14</i><i>15</i><i>16</i><i>17</i><i>18</i><i>19</i><i>20</i><i>21</i><i>22</i><i>23</i><i>24</i><i>25</i><i>26</i><i>27</i><i>28</i><i>29</i><i>30</i><i>31</i></div></article>
    <article class="month"><h2>Junho</h2><div class="weekdays"><span>D</span><span>S</span><span>T</span><span>Q</span><span>Q</span><span>S</span><span>S</span></div>
      <div class="days"><i>1</i><i>2</i><i>3</i><i>4</i><i>5</i><i>6</i><i>7</i><i>8</i><i>9</i><i>10</i><i>11</i><i>12</i><i>13</i><i>14</i><i>15</i><i>16</i><i>17</i><i>18</i><i>19</i><i>20</i><i>21</i><i>22</i><i>23</i><i>24</i><i>25</i><i>26</i><i>27</i><i>28</i><i>29</i><i>30</i></div></article>

    <article class="month"><h2>Julho</h2><div class="weekdays"><span>D</span><span>S</span><span>T</span><span>Q</span><span>Q</span><span>S</span><span>S</span></div>
      <div class="days"><i class="o2">1</i><i>2</i><i>3</i><i>4</i><i>5</i><i>6</i><i>7</i><i>8</i><i>9</i><i>10</i><i>11</i><i>12</i><i>13</i><i>14</i><i>15</i><i>16</i><i>17</i><i>18</i><i>19</i><i>20</i><i>21</i><i>22</i><i>23</i><i>24</i><i>25</i><i>26</i><i>27</i><i>28</i><i>29</i><i>30</i><i>31</i></div></article>
    <article class="month"><h2>Agosto</h2><div class="weekdays"><span>D</span><span>S</span><span>T</span><span>Q</span><span>Q</span><span>S</span><span>S</span></div>
      <div class="days"><i class="o5">1</i><i>2</i><i>3</i><i>4</i><i>5</i><i>6</i><i>7</i><i>8</i><i>9</i><i>10</i><i>11</i><i>12</i><i>13</i><i>14</i><i>15</i><i>16</i><i>17</i><i>18</i><i>19</i><i>20</i><i>21</i><i>22</i><i>23</i><i>24</i><i>25</i><i>26</i><i>27</i><i>28</i><i>29</i><i>30</i><i>31</i></div></article>
    <article class="month"><h2>Setembro</h2><div class="weekdays"><span>D</span><span>S</span><span>T</span><span>Q</span><span>Q</span><span>S</span><span>S</span></div>
      <div class="days"><i class="o1">1</i><i>2</i><i>3</i><i>4</i><i>5</i><i>6</i><i>7</i><i>8</i><i>9</i><i>10</i><i>11</i><i>12</i><i>13</i><i>14</i><i>15</i><i>16</i><i>17</i><i>18</i><i>19</i><i>20</i><i>21</i><i>22</i><i>23</i><i>24</i><i>25</i><i>26</i><i>27</i><i>28</i><i>29</i><i>30</i></div></article>

    <article class="month"><h2>Outubro</h2><div class="weekdays"><span>D</span><span>S</span><span>T</span><span>Q</span><span>Q</span><span>S</span><span>S</span></div>
      <div class="days"><i class="o3">1</i><i>2</i><i>3</i><i>4</i><i>5</i><i>6</i><i>7</i><i>8</i><i>9</i><i>10</i><i>11</i><i>12</i><i>13</i><i>14</i><i>15</i><i>16</i><i>17</i><i>18</i><i>19</i><i>20</i><i>21</i><i>22</i><i>23</i><i>24</i><i>25</i><i>26</i><i>27</i><i>28</i><i>29</i><i>30</i><i>31</i></div></article>
    <article class="month"><h2>Novembro</h2><div class="weekdays"><span>D</span><span>S</span><span>T</span><span>Q</span><span>Q</span><span>S</span><span>S</span></div>
      <div class="days"><i class="o6">1</i><i>2</i><i>3</i><i>4</i><i>5</i><i>6</i><i>7</i><i>8</i><i>9</i><i>10</i><i>11</i><i>12</i><i>13</i><i>14</i><i>15</i><i>16</i><i>17</i><i>18</i><i>19</i><i>20</i><i>21</i><i>22</i><i>23</i><i>24</i><i>25</i><i>26</i><i>27</i><i>28</i><i>29</i><i>30</i></div></article>
    <article class="month"><h2>Dezembro</h2><div class="weekdays"><span>D</span><span>S</span><span>T</span><span>Q</span><span>Q</span><span>S</span><span>S</span></div>
      <div class="days"><i class="o1">1</i><i>2</i><i>3</i><i>4</i><i>5</i><i>6</i><i>7</i><i>8</i><i>9</i><i>10</i><i>11</i><i>12</i><i>13</i><i>14</i><i>15</i><i>16</i><i>17</i><i>18</i><i>19</i><i>20</i><i>21</i><i>22</i><i>23</i><i>24</i><i>25</i><i>26</i><i>27</i><i>28</i><i>29</i><i>30</i><i>31</i></div></article>
  </section>
</main>
</body>
</html>
```